Bright Towns Forum PowerPoint Design Template and Sample Deck

The Bright Towns Forum is an international organization that seeks to improve the livability, workability and sustainability of the world’s cities.
We seek a versatile PowerPoint design template with 10 slide types plus a “self-documenting” sample deck. Your design will be used in keynote speeches and workshops around the world.
After the contest is completed, we will ask the winning designer to add 10-20 additional slide types for $75 per slide. We also seek a long-term relationship whereby we can request “custom” slides and/or ask the designer to touch up the slides we build to make them better.
FILES. We have uploaded several files:
2. PALETTE. Shows our official colors.
3 LOGOS. Several individual files with different variations of our logo. Some with our motto, some without.
2. SAMPLE SLIDES. Because we were unable to successfully upload our sample deck, we are making it available via this FileNook link:
https://www.filenook-example.com/s/k7qrtmzp2wd9hxa/The%20Bright%20Towns%20Forum%20Design%20Contest%20Notes.docx?dl=0
Target Market(s)
Mayors, department heads, CIOs, senior executives from technology companies
Industry/Entity Type
Information Technology
Colors
Designer to choose colors to be used in the design.
Requirements
Must have
- Please see uploaded Word document for requirements, nice to haves and should not haves and uploaded palette for color preferences.
Nice to have
- see above
Should not have
- see above

```html
<!DOCTYPE html>
<html lang="en">
<head>
<meta charset="utf-8">
<title>Bright Towns Forum – Sample Deck Slides</title>
<link rel="stylesheet" href="https://fonts.googleapis.com/css2?family=Questrial&family=Raleway:wght@300;400&display=swap">
<style>
  :root {
    --page: #f2f2f2;
    --white: #ffffff;
    --navy: #1d3d78;
    --blue: #2d5c9c;
    --mid: #4f7fb8;
    --light: #9dbfdd;
    --pale: #d6e5f1;
    --text: #6f7f93;
    --ink: #1f3c70;
    --shadow: 0 10px 22px rgba(0,0,0,.18);
  }
  * { margin: 0; padding: 0; box-sizing: border-box; }
  html, body { width: 774px; height: 1200px; overflow: hidden; background: var(--page); }
  body { position: relative; font-family: "Questrial", "Century Gothic", sans-serif; color: var(--text); }
  .slide { position: absolute; width: 301px; height: 168px; background: var(--white); box-shadow: var(--shadow); overflow: hidden; }
  .col-left { left: 70px; } .col-right { left: 402px; }
  .row-1 { top: 29px; } .row-2 { top: 241px; } .row-3 { top: 451px; }
  .abs { position: absolute; }
  .tiny { font-size: 3.4px; line-height: 1.45; color: var(--text); }
  .photo-fill { position: absolute; }

  /* section slide */
  .section-block { left: 40px; top: 0; width: 62px; height: 131px; background: var(--blue); }
  .section-band { left: 0; top: 66px; width: 301px; height: 65px; background: linear-gradient(90deg, #21467f 0%, #3c74b4 45%, #1a3667 100%); }
  .section-number { left: 40px; top: 66px; width: 62px; height: 65px; background: rgba(29,61,120,.85); color: var(--white); padding: 20px 0 0 10px; font-size: 17px; line-height: 1; }
  .section-number small { display: block; font-size: 3.4px; letter-spacing: .3px; margin-top: 3px; opacity: .8; }
  .section-title { right: 8px; top: 40px; font-size: 8.5px; color: var(--blue); }
  .section-sub { right: 8px; top: 53px; text-align: right; }

  /* icon slide */
  .icon-photo { inset: 0 0 43px 0; background: radial-gradient(ellipse at 50% 85%, #8fb0d4 0%, #2f5b98 35%, #1c3a72 75%); }
  .icon-strip { left: 0; right: 0; bottom: 0; height: 43px; background: #e9eff6; }
  .icon-circle { top: 44px; width: 36px; height: 36px; border-radius: 50%; border: 1px solid rgba(255,255,255,.45); background: rgba(255,255,255,.08); box-shadow: 0 0 0 3px rgba(255,255,255,.08); color: var(--white); font-size: 4.6px; display: flex; align-items: center; justify-content: center; letter-spacing: .2px; }
  .icon-title { left: 0; right: 0; top: 130px; text-align: center; font-size: 6.5px; color: var(--blue); letter-spacing: .3px; }
  .icon-sub { left: 25px; right: 25px; top: 140px; text-align: center; }

  /* contents header */
  .contents-tab { left: 0; top: 0; width: 7px; height: 22px; background: var(--navy); }
  .contents-corner { right: 0; top: 0; width: 4px; height: 22px; background: var(--navy); clip-path: polygon(40% 0,100% 0,100% 100%); }
  .contents-title { left: 14px; top: 6px; font-size: 8.5px; color: var(--navy); }
  .contents-sub { left: 14px; top: 16px; font-size: 2.8px; }

  .tag { left: 55px; top: 33px; background: var(--navy); color: var(--white); font-size: 4px; padding: 1px 3px; }
  .chart-caption { left: 0; right: 0; top: 101px; text-align: center; }
  .stat-title { left: 40px; top: 124px; font-size: 5px; color: var(--navy); }
  .stat-value { left: 230px; top: 122px; font-size: 7.5px; color: var(--navy); }
  .stat-text { left: 26px; right: 26px; top: 135px; }

  .bullet-title { left: 28px; top: 70px; font-size: 5.5px; color: var(--navy); }
  .bullet-title::before { content: ""; position: absolute; left: -9px; top: 1px; width: 3px; height: 5px; border-radius: 2px; background: var(--navy); }
  .bullet-text { left: 28px; width: 96px; }
  .bullet-text::before { content: ""; position: absolute; left: -6px; top: 1px; width: 2px; height: 2px; border-radius: 50%; background: var(--navy); }
  .legend { left: 225px; top: 68px; font-size: 3.4px; color: var(--text); }
  .legend li { list-style: none; margin-bottom: 10.5px; position: relative; padding-left: 8px; }
  .legend i { position: absolute; left: 0; top: .5px; width: 3px; height: 3px; border-radius: 50%; }

  /* progress slide */
  .progress-label { font-size: 4.2px; color: var(--white); letter-spacing: .2px; }
  .progress-text { width: 95px; color: #c9d8ea; }
  .progress-value { font-size: 5px; color: var(--ink); width: 28px; text-align: center; }
  .progress-name { left: 14px; top: 132px; font-size: 5.2px; color: var(--blue); line-height: 1.4; }
  .progress-name::before { content: ""; position: absolute; left: 0; top: -3px; width: 11px; height: 2px; background: var(--navy); }

  .about-title { left: 0; right: 0; top: 41px; text-align: center; font-size: 6.5px; color: var(--navy); }
  .about-text { left: 35px; right: 35px; top: 51px; text-align: center; }

  /* closing */
  .closing { left: 70px; top: 689px; width: 630px; height: 354px; box-shadow: var(--shadow); overflow: hidden; }
  .closing-photo { inset: 0; background: linear-gradient(180deg, #4f8fb3 0%, #c5dfe2 28%, #9cc4d4 52%, #3f71a4 66%, #1f427d 78%, #3d76aa 88%, #2c5d95 100%); }
  .closing-rule { left: 217px; top: 64px; width: 168px; height: 1px; background: rgba(30,60,110,.55); }
  .closing-title { left: 0; right: 0; top: 73px; text-align: center; font-family: "Raleway", "Century Gothic", sans-serif; font-weight: 300; font-size: 29px; letter-spacing: 1px; color: #2a5b8f; }
  .ring { position: absolute; border-radius: 50%; border: 1px solid rgba(70,110,150,.45); }
</style>
</head>
<body>

<!-- Section divider -->
<section class="slide col-left row-1">
  <div class="abs section-block"></div>
  <div class="abs section-band photo-fill" role="img" aria-label="Photo of a lake at dusk with hills on the horizon"></div>
  <div class="abs section-number">04<small>PART TITLE</small></div>
  <h2 class="abs section-title">Pixelcraft 6</h2>
  <p class="abs tiny section-sub">Plan tomorrow's streets with care today and share what works.</p>
</section>

<!-- Icon row slide -->
<section class="slide col-right row-1">
  <div class="abs icon-photo photo-fill" role="img" aria-label="Photo of a snowy mountain peak under a blue sky"></div>
  <div class="abs icon-strip"></div>
  <div class="abs icon-circle" style="left:28px">PHOTO</div>
  <div class="abs icon-circle" style="left:97px">SEARCHLY</div>
  <div class="abs icon-circle" style="left:166px">POWER</div>
  <div class="abs icon-circle" style="left:235px">ARTISOFT</div>
  <h2 class="abs icon-title">VECTORLY STUDIO</h2>
  <p class="abs tiny icon-sub">Good towns grow from small steps taken together every single day by people who care. Share your plans early and build on what works.</p>
</section>

<!-- Peak chart slide -->
<section class="slide col-left row-2">
  <div class="abs contents-tab"></div><div class="abs contents-corner"></div>
  <h2 class="abs contents-title">CONTENTS</h2>
  <p class="abs contents-sub">A short note on the numbers below.</p>
  <span class="abs tag">SEARCHLY</span>
  <svg class="abs" style="left:50px;top:40px" width="200" height="60" viewBox="0 0 200 60">
    <g font-size="3.6" fill="#2d5c9c" font-family="Questrial, sans-serif" text-anchor="middle">
      <text x="22" y="15">3.2</text><text x="49" y="23">2.5</text><text x="76" y="31">1.8</text>
      <text x="103" y="5">4.5</text><text x="130" y="17">3.4</text><text x="157" y="21">3.1</text>
    </g>
    <g>
      <path d="M4 56 Q18 40 22 18 Q26 40 40 56Z" fill="#4f7fb8"/>
      <path d="M31 56 Q45 44 49 26 Q53 44 67 56Z" fill="#6f98c7"/>
      <path d="M58 56 Q72 48 76 34 Q80 48 94 56Z" fill="#4f7fb8"/>
      <path d="M85 56 Q99 36 103 8 Q107 36 121 56Z" fill="#1d3d78"/>
      <path d="M112 56 Q126 40 130 20 Q134 40 148 56Z" fill="#4f7fb8"/>
      <path d="M139 56 Q153 42 157 24 Q161 42 175 56Z" fill="#6f98c7"/>
    </g>
    <line x1="0" y1="56" x2="180" y2="56" stroke="#c9d6e4" stroke-width=".4"/>
  </svg>
  <p class="abs tiny chart-caption">Each peak shows one year of growth in town services.</p>
  <svg class="abs" style="left:26px;top:123px" width="9" height="7" viewBox="0 0 9 7"><path d="M4.5 0 9 7H0Z" fill="#1d3d78"/></svg>
  <h3 class="abs stat-title">VECTORLY STUDIO</h3>
  <svg class="abs" style="left:218px;top:125px" width="9" height="4" viewBox="0 0 9 4"><path d="M0 2H8M6 0 8 2 6 4" stroke="#1d3d78" stroke-width=".6" fill="none"/></svg>
  <span class="abs stat-value">35,264$</span>
  <p class="abs tiny stat-text">Towns that share data save time and money, and their residents notice the change in daily life.</p>
</section>

<!-- Pie chart slide -->
<section class="slide col-right row-2">
  <div class="abs contents-tab"></div><div class="abs contents-corner"></div>
  <h2 class="abs contents-title">CONTENTS</h2>
  <p class="abs contents-sub">A short note on the numbers below.</p>
  <h3 class="abs bullet-title">SEARCHLY BROWSER</h3>
  <p class="abs tiny bullet-text" style="top:82px">Open data helps each town plan better roads, cleaner air and safer streets for all.</p>
  <p class="abs tiny bullet-text" style="top:106px">Small pilots show what works before a larger rollout begins.</p>
  <svg class="abs" style="left:125px;top:35px" width="100" height="100" viewBox="-20 -20 100 100">
    <circle cx="30" cy="30" r="48" fill="none" stroke="#eef2f7" stroke-width=".6"/>
    <circle cx="30" cy="30" r="38" fill="none" stroke="#e3eaf2" stroke-width=".5"/>
    <circle cx="30" cy="-10" r="1" fill="#9dbfdd"/>
    <circle cx="30" cy="70" r="1.5" fill="none" stroke="#c9d6e4" stroke-width=".4"/>
    <path d="M30 30L30 4A26 26 0 0 1 49 47.7Z" fill="#1d3d78"/>
    <path d="M30 30L49 47.7A26 26 0 0 1 5.9 39.7Z" fill="#2d5c9c"/>
    <path d="M30 30L5.9 39.7A26 26 0 0 1 9 14.7Z" fill="#7aa6cf"/>
    <path d="M30 30L9 14.7A26 26 0 0 1 30 4Z" fill="#d6e5f1"/>
    <g font-family="Questrial, sans-serif" font-size="4" fill="#fff" text-anchor="middle">
      <text x="40" y="26">3.7</text><text x="28" y="46">3.2</text><text x="13" y="31" fill="#1d3d78">1.6</text>
    </g>
  </svg>
  <ul class="abs legend">
    <li><i style="background:#1d3d78"></i>Searchly Browser</li>
    <li><i style="background:#2d5c9c"></i>Pixelcraft 6</li>
    <li><i style="background:#7aa6cf"></i>Vectorly Studio</li>
    <li><i style="background:#d6e5f1;border:.3px solid #9dbfdd"></i>SlideMaker 2013</li>
  </ul>
</section>

<!-- Progress slide -->
<section class="slide col-left row-3">
  <svg class="abs" style="left:0;top:0" width="301" height="168" viewBox="0 0 301 168">
    <defs><linearGradient id="progressBlue" x1="0" y1="0" x2="1" y2="1"><stop offset="0" stop-color="#2d5c9c"/><stop offset="1" stop-color="#1f437f"/></linearGradient></defs>
    <path d="M88 0Q70 84 116 168H301V0Z" fill="url(#progressBlue)"/>
    <g fill="#fff" stroke="#e3eaf2" stroke-width="1">
      <circle cx="89" cy="31" r="18"/><circle cx="101" cy="80" r="18"/><circle cx="113" cy="129" r="18"/>
    </g>
    <g fill="none" stroke-width="1.2" stroke-linecap="round">
      <circle cx="89" cy="31" r="12" stroke="#e3eaf2"/><circle cx="89" cy="31" r="12" stroke="#2d5c9c" stroke-dasharray="60.3 75.4" transform="rotate(-90 89 31)"/>
      <circle cx="101" cy="80" r="12" stroke="#e3eaf2"/><circle cx="101" cy="80" r="12" stroke="#4f7fb8" stroke-dasharray="25.6 75.4" transform="rotate(-90 101 80)"/>
      <circle cx="113" cy="129" r="12" stroke="#e3eaf2"/><circle cx="113" cy="129" r="12" stroke="#4f7fb8" stroke-dasharray="48.3 75.4" transform="rotate(-90 113 129)"/>
    </g>
    <g fill="#5d84b8"><path d="M115 29l3 2-3 2Z"/><path d="M127 78l3 2-3 2Z"/><path d="M139 127l3 2-3 2Z"/></g>
  </svg>
  <span class="abs progress-value" style="left:75px;top:28px">80%</span>
  <span class="abs progress-value" style="left:87px;top:77px">34%</span>
  <span class="abs progress-value" style="left:99px;top:126px">64%</span>
  <h3 class="abs progress-label" style="left:128px;top:22px">PANES OS</h3>
  <p class="abs tiny progress-text" style="left:128px;top:29px">Shared tools help teams plan faster and act with confidence.</p>
  <h3 class="abs progress-label" style="left:140px;top:71px">PIXELCRAFT</h3>
  <p class="abs tiny progress-text" style="left:140px;top:78px">Shared tools help teams plan faster and act with confidence.</p>
  <h3 class="abs progress-label" style="left:152px;top:120px">VECTORLY STUDIO</h3>
  <p class="abs tiny progress-text" style="left:152px;top:127px">Shared tools help teams plan faster and act with confidence.</p>
  <h2 class="abs progress-name">VECTORLY<br>STUDIO</h2>
</section>

<!-- Line chart slide -->
<section class="slide col-right row-3">
  <div class="abs contents-tab"></div><div class="abs contents-corner"></div>
  <h2 class="abs contents-title">CONTENTS</h2>
  <p class="abs contents-sub">A short note on the numbers below.</p>
  <h3 class="abs about-title">ABOUT OUR COMPANY</h3>
  <p class="abs tiny about-text">Our forum links mayors and leaders who want towns that work better for the people living in them.</p>
  <svg class="abs" style="left:40px;top:70px" width="210" height="82" viewBox="0 0 210 82">
    <g stroke="#eef2f7" stroke-width=".4">
      <line x1="12" y1="8" x2="200" y2="8"/><line x1="12" y1="20" x2="200" y2="20"/><line x1="12" y1="32" x2="200" y2="32"/>
      <line x1="12" y1="44" x2="200" y2="44"/><line x1="12" y1="56" x2="200" y2="56"/><line x1="12" y1="68" x2="200" y2="68"/>
    </g>
    <g font-family="Questrial, sans-serif" font-size="3" fill="#8a98aa" text-anchor="end">
      <text x="8" y="9">5</text><text x="8" y="21">4</text><text x="8" y="33">3</text><text x="8" y="45">2</text><text x="8" y="57">1</text><text x="8" y="69">0</text>
    </g>
    <g font-family="Questrial, sans-serif" font-size="3" fill="#8a98aa" text-anchor="middle">
      <text x="20" y="76">1</text><text x="36" y="76">2</text><text x="52" y="76">3</text><text x="68" y="76">4</text><text x="84" y="76">5</text><text x="100" y="76">6</text>
      <text x="116" y="76">7</text><text x="132" y="76">8</text><text x="148" y="76">9</text><text x="164" y="76">10</text><text x="180" y="76">11</text><text x="196" y="76">12</text>
    </g>
    <path d="M20 17.6C28 24 28 38 36 38S44 28 52 27.2 60 14 68 14 76 39 84 39.2 92 15 100 15.2 108 46 116 46.4 124 34 132 34.4 140 44 148 44 156 44 164 44 172 32 180 32 188 16 196 5.6" fill="none" stroke="#7aa6cf" stroke-width=".9"/>
    <g fill="#fff" stroke="#7aa6cf" stroke-width=".6">
      <circle cx="20" cy="17.6" r="1.2"/><circle cx="36" cy="38" r="1.2"/><circle cx="52" cy="27.2" r="1.2"/><circle cx="68" cy="14" r="1.2"/>
      <circle cx="84" cy="39.2" r="1.2"/><circle cx="100" cy="15.2" r="1.2"/><circle cx="116" cy="46.4" r="1.2"/><circle cx="132" cy="34.4" r="1.2"/>
      <circle cx="148" cy="44" r="1.2"/><circle cx="164" cy="44" r="1.2"/><circle cx="180" cy="32" r="1.2"/>
    </g>
    <circle cx="196" cy="5.6" r="1.5" fill="#1d3d78"/>
    <text x="196" y="2.5" font-family="Questrial, sans-serif" font-size="4" fill="#1d3d78" text-anchor="middle">5.2</text>
  </svg>
</section>

<!-- Closing slide -->
<section class="abs closing">
  <div class="abs closing-photo photo-fill" role="img" aria-label="Photo of a snow-capped mountain across a calm lake under a cloudy sky"></div>
  <span class="ring" style="left:385px;top:-10px;width:38px;height:38px;top:-9px;transform:translateY(0)"></span>
  <span class="ring" style="left:413px;top:28px;width:14px;height:14px"></span>
  <span class="ring" style="left:186px;top:77px;width:18px;height:18px"></span>
  <div class="abs closing-rule"></div>
  <h1 class="abs closing-title">THANK YOU</h1>
</section>

</body>
</html>
```